Baby Food product, packaging design

Tot Harvest is a home-made style, frozen baby food service. The business provides frozen puree and textured baby food blends in ice-cube like freezer trays.

I am after 9 designs to be used as my front of package sticker, this will include the product name, logo, nutritional panel and other things as per the uploaded document.

***On my document I forgot to add that the second container is 9cm in width (Across) and 13cm in length (down).

```html
<!DOCTYPE html>
<html lang="en">
<head>
<meta charset="utf-8">
<title>Tot Harvest – Sunny Medley label</title>
<link rel="stylesheet" href="https://fonts.googleapis.com/css2?family=Patrick+Hand&family=Gochi+Hand&family=Arimo:wght@400;700&display=swap">
<style>
  :root {
    --page: #ffffff;
    --panel-grey: #efeff1;
    --ribbon: #e2a59d;
    --ribbon-fold: #8a8a8a;
    --teal-dark: #18a39f;
    --teal-light: #5cc8d6;
    --sky: #2ec0e0;
    --ink: #3a3a3a;
    --red: #c8202e;
    --freezer-blue: #3aa8de;
    --veg-orange: #f08a2c;
    --veg-purple: #8e2f55;
  }
  * { box-sizing: border-box; margin: 0; padding: 0; }
  html, body { width: 1200px; height: 1200px; overflow: hidden; background: var(--page); }
  .canvas { position: relative; width: 1200px; height: 1200px; font-family: "Arimo", Arial, sans-serif; }

  .left-panel { position: absolute; left: 76px; top: 63px; width: 497px; height: 1054px; overflow: hidden; }
  .left-panel svg.backdrop { position: absolute; inset: 0; }

  .brand { position: absolute; left: 40px; top: 160px; width: 417px; display: flex; align-items: center; justify-content: center; gap: 16px; }
  .brand-dot { width: 40px; height: 40px; border-radius: 50%; background: var(--sky); flex: none; }
  .brand-name { font-family: "Arimo", Arial, sans-serif; font-weight: 700; font-size: 46px; color: var(--ink); }

  .instructions-title { position: absolute; left: 28px; top: 425px; font-family: "Gochi Hand", cursive;
    font-weight: 400; font-size: 60px; color: var(--ink); }

  .step-ribbon { position: absolute; left: 97px; width: 414px; height: 108px; background: var(--ribbon);
    font-family: "Patrick Hand", cursive; font-size: 30px; line-height: 1.3; color: #fff;
    padding: 12px 0 0 40px; letter-spacing: 1px; }
  .step-ribbon::after { content: ""; position: absolute; right: 0; bottom: -14px; border-top: 14px solid var(--ribbon-fold); border-right: 14px solid transparent; }
  .step-badge { position: absolute; left: 6px; width: 118px; height: 118px; border-radius: 50%; background: var(--teal-dark);
    display: flex; align-items: center; justify-content: center; }
  .step-badge span { width: 72px; height: 72px; border-radius: 50%; background: var(--teal-light); color: #fff;
    font-family: "Patrick Hand", cursive; font-size: 46px; display: flex; align-items: center; justify-content: center; }

  .right-panel { position: absolute; left: 573px; top: 63px; width: 556px; height: 1054px; background: var(--panel-grey); }

  .product-title { position: absolute; left: 47px; top: 41px; width: 436px; height: 125px; border-radius: 20px;
    background: var(--red); color: #fff; font-weight: 700; font-size: 50px; display: flex; align-items: center; justify-content: center; }
  .product-blend { position: absolute; left: 0; width: 556px; top: 180px; text-align: center; color: var(--red);
    font-size: 31px; font-weight: 700; line-height: 1.22; }

  .nutrition-heading { position: absolute; left: 136px; top: 283px; color: var(--red); font-weight: 700; font-size: 20px; }
  .nutrition-sub { display: block; font-size: 13px; line-height: 1.25; }
  .nutrition-sub small { font-weight: 400; font-size: 13px; }

  .nutrition-table { position: absolute; left: 110px; top: 350px; width: 408px; height: 287px; }
  .nutrition-label { position: absolute; color: var(--red); font-weight: 700; font-size: 17px; line-height: 1.15; }
  .nutrition-col { position: absolute; color: var(--red); font-weight: 700; font-size: 18px; line-height: 1.2; }

  .veg-characters { position: absolute; left: 12px; top: 677px; width: 525px; height: 170px; border-radius: 40px;
    background: linear-gradient(90deg, var(--veg-orange), var(--red) 30%, #9a5a40 50%, var(--veg-orange) 70%, var(--veg-purple)); opacity: .85; }
  .veg-ground { position: absolute; left: 50px; top: 852px; width: 470px; height: 4px; background: #9a9a9a; border-radius: 2px; }

  .storage-pill { position: absolute; left: 168px; top: 878px; width: 244px; height: 43px; border-radius: 12px;
    background: var(--freezer-blue); border: 2px solid #2a7fb0; color: #1c2a3a; font-size: 17px; font-weight: 700;
    display: flex; align-items: center; justify-content: center; }
  .allergen-note { position: absolute; left: 0; width: 556px; top: 928px; text-align: center; color: var(--red);
    font-size: 16px; font-weight: 700; line-height: 1.65; }
  .claims { position: absolute; left: 0; width: 556px; top: 988px; text-align: center; color: var(--ink);
    font-size: 16px; font-weight: 700; line-height: 1.5; }
</style>
</head>
<body>
<div class="canvas">

  <section class="left-panel">
    <svg class="backdrop" width="497" height="1054" viewBox="0 0 497 1054" aria-hidden="true">
      <defs>
        <linearGradient id="coralWash" x1="0" y1="0" x2="1" y2="0">
          <stop offset="0" stop-color="#d88b84"/>
          <stop offset="1" stop-color="#e9b7b1"/>
        </linearGradient>
        <linearGradient id="butterWash" x1="0" y1="0" x2="1" y2="0">
          <stop offset="0" stop-color="#e4e07a"/>
          <stop offset="1" stop-color="#e7d79a"/>
        </linearGradient>
      </defs>
      <rect width="497" height="1054" fill="url(#coralWash)"/>
      <polygon points="0,0 60,0 497,270 497,1054 360,1054 0,790" fill="url(#butterWash)"/>
    </svg>

    <div class="brand"><span class="brand-dot"></span><span class="brand-name">Tot Harvest</span></div>

    <h2 class="instructions-title">Instructions :</h2>

    <div class="step-ribbon" style="top:521px;">pop out the design<br>number of cubes</div>
    <div class="step-badge" style="top:518px;"><span>1</span></div>

    <div class="step-ribbon" style="top:684px;">Heat in the microwave<br>on high for 1-2 minutes</div>
    <div class="step-badge" style="top:678px;"><span>2</span></div>

    <div class="step-ribbon" style="top:841px;">Stir and allow to cool<br>before serving.</div>
    <div class="step-badge" style="top:834px;"><span>3</span></div>
  </section>

  <section class="right-panel">
    <h1 class="product-title">Sunny Medley</h1>
    <p class="product-blend">pumpkin, beetroot, carrot<br>red capsicum &amp; sweet potato</p>

    <div class="nutrition-heading">Nutritional Information
      <span class="nutrition-sub">Servings per package 3<br>Serving size 2 × 50g cubs <small>(100g)</small></span>
    </div>

    <div class="nutrition-table">
      <svg width="408" height="287" viewBox="0 0 408 287" aria-hidden="true">
        <g stroke="#111" stroke-width="3">
          <line x1="0" y1="0" x2="408" y2="0"/>
          <line x1="0" y1="123" x2="408" y2="123"/>
          <line x1="0" y1="174" x2="408" y2="174"/>
          <line x1="0" y1="224" x2="408" y2="224"/>
          <line x1="168" y1="0" x2="168" y2="287"/>
          <line x1="298" y1="0" x2="298" y2="280"/>
        </g>
      </svg>
      <div class="nutrition-col" style="left:184px; top:14px;">per 50g<br>cube</div>
      <div class="nutrition-col" style="left:312px; top:14px;">per 100g<br>serving</div>
      <div class="nutrition-label" style="left:8px; top:78px;">Energy<br>Protein</div>
      <div class="nutrition-label" style="left:6px; top:129px;">Total fat<br>-Saturated</div>
      <div class="nutrition-label" style="left:6px; top:179px;">Carbohydrate<br>-Sugars</div>
      <div class="nutrition-label" style="left:8px; top:231px;">Dietary fibre<br>Sodium</div>
    </div>

    <div class="veg-characters" role="img" aria-label="Illustration of cartoon vegetables: a carrot holding a 100% natural sign, a red capsicum, a sweet potato, a yellow capsicum and a beetroot"></div>
    <div class="veg-ground"></div>

    <div class="storage-pill">Store in freezer - 18 c.</div>
    <p class="allergen-note">Produced on equipment that also processest<br>fish, wheat, and milk products.</p>
    <p class="claims">No added salt, no added suger<br>100&nbsp;&nbsp;&nbsp;Australian product, NT made, dietitian created</p>
  </section>

</div>
</body>
</html>
```